Business card for a Exhibition booth fabrication company

Hi. My company would like to change our corporate name card. We are an events and Exhibition stand builder company. We would like our corporate name card to resonate what we do. I need someone to create something unique that relates to the industry that I am in. The graphic designer should be creative to incorporate the elements of my industry and try to blend in well in the design of the card. Our aim is to ensure that we are unique and our card can look different from our competitors.
Updates

Target Market(s)

Marketing and events manager from all companies

Contact Information for Business Card

The business card should have the following details:
Name
Job Title
Email
Website

Colors

Designer to choose colors to be used in the design.

Requirements
Must have
• The card must be look something that is relevant to the service that I am providing. My website is: www.velmora-buildworks.com
• You can see my website to get more information on what service that I am doing
Nice to have
• On the back of my card, I would like to have a globe image with the incorporation of my company logo. This is to indicate that my services can be done in any part of the world.

```html
<!DOCTYPE html>
<html lang="en">
<head>
<meta charset="utf-8">
<title>Velmora Buildworks — Business Card</title>
<link rel="stylesheet" href="https://fonts.googleapis.com/css2?family=Montserrat:wght@600&family=Open+Sans:wght@400;600&display=swap">
<style>
  :root {
    --page: #2b2b2d;
    --card-white: #f6f6f7;
    --card-dark: #4a4a4d;
    --brand-red: #e3202a;
    --swoosh-grey: #c7c8ca;
    --text-light: #ffffff;
    --text-dark: #4a4a4d;
    --map-tone: #5a5a5e;
  }
  * { box-sizing: border-box; margin: 0; padding: 0; }
  html, body { width: 1200px; height: 900px; overflow: hidden; }
  body {
    background: var(--page);
    position: relative;
    font-family: "Open Sans", Arial, sans-serif;
  }
  .card {
    position: absolute;
    width: 680px;
    height: 390px;
    border-radius: 22px;
    overflow: hidden;
    box-shadow: 0 14px 30px rgba(0,0,0,0.45);
  }
  .card-front { left: 60px; top: 50px; background: var(--card-white); }
  .card-back  { left: 460px; top: 460px; background: var(--card-dark); }

  .front-waves { position: absolute; inset: 0; width: 100%; height: 100%; }

  .brand {
    position: absolute;
    display: flex;
    align-items: center;
    gap: 12px;
    font-family: "Montserrat", Arial, sans-serif;
    font-weight: 600;
    letter-spacing: 0.14em;
    white-space: nowrap;
  }
  .brand-dot {
    width: 26px; height: 26px;
    border-radius: 50%;
    background: var(--brand-red);
    flex: none;
  }
  .card-front .brand {
    left: 50px; top: 96px;
    font-size: 26px;
    line-height: 1.25;
    color: var(--text-dark);
  }

  .contact {
    position: absolute;
    right: 34px;
    top: 182px;
    text-align: right;
    color: var(--text-light);
    font-size: 13.5px;
    line-height: 1.55;
  }
  .contact-address { margin-bottom: 8px; }
  .contact-line { display: flex; justify-content: flex-end; align-items: center; gap: 8px; }
  .contact-icon { width: 12px; height: 12px; flex: none; }

  .person { position: absolute; left: 46px; bottom: 30px; }
  .person-name {
    font-weight: 600;
    font-size: 20px;
    color: var(--text-light);
    letter-spacing: 0.02em;
  }
  .person-title { font-size: 16px; color: var(--brand-red); }

  .world-map {
    position: absolute;
    left: 70px; top: 40px;
    width: 560px; height: 310px;
    border-radius: 40px;
    background: radial-gradient(ellipse at center, var(--map-tone) 0%, rgba(90,90,94,0.5) 55%, rgba(74,74,77,0) 80%);
  }
  .card-back .brand {
    left: 50%; top: 50%;
    transform: translate(-50%, -50%);
    font-size: 30px;
    color: var(--text-light);
  }
</style>
</head>
<body>

<section class="card card-front" aria-label="Business card front">
  <svg class="front-waves" viewBox="0 0 680 390" preserveAspectRatio="none" aria-hidden="true">
    <path d="M560 0 Q470 205 0 282 L0 390 L680 390 L680 0 Z" fill="var(--swoosh-grey)"/>
    <path d="M588 0 Q500 222 0 292 L0 390 L680 390 L680 0 Z" fill="var(--brand-red)"/>
    <path d="M612 0 Q560 200 0 318 L0 390 L680 390 L680 0 Z" fill="var(--card-dark)"/>
  </svg>

  <div class="brand"><span class="brand-dot"></span><span class="brand-name">VELMORA<br>BUILDWORKS</span></div>

  <div class="contact">
    <p class="contact-address">P.O. Box 4821, West Bay,<br>Corniche Road Doha - Qatar</p>
    <p class="contact-line">+974 5550 1234
      <svg class="contact-icon" viewBox="0 0 12 12" aria-hidden="true"><path d="M2 1 L4.5 1 L5.5 3.5 L4 4.6 Q5 7 7.4 8 L8.5 6.5 L11 7.5 L11 10 Q6 11 2.5 7 Q0.8 4 2 1 Z" fill="var(--brand-red)"/></svg>
    </p>
    <p class="contact-line">info@velmora-buildworks.com
      <svg class="contact-icon" viewBox="0 0 12 12" aria-hidden="true"><rect x="0.5" y="2" width="11" height="8" rx="1" fill="var(--brand-red)"/><path d="M1 2.5 L6 6.5 L11 2.5" stroke="var(--card-dark)" fill="none"/></svg>
    </p>
    <p class="contact-line">www.velmora-buildworks.com
      <svg class="contact-icon" viewBox="0 0 12 12" aria-hidden="true"><circle cx="6" cy="6" r="5" fill="none" stroke="var(--brand-red)" stroke-width="1.3"/><ellipse cx="6" cy="6" rx="2" ry="5" fill="none" stroke="var(--brand-red)"/><path d="M1 6 H11" stroke="var(--brand-red)"/></svg>
    </p>
  </div>

  <div class="person">
    <p class="person-name">DANIEL REYES</p>
    <p class="person-title">President</p>
  </div>
</section>

<section class="card card-back" aria-label="Business card back">
  <div class="world-map" role="img" aria-label="Faint dotted world map spread across the card"></div>
  <div class="brand"><span class="brand-dot"></span>VELMORA BUILDWORKS</div>
</section>

</body>
</html>
```